Diverse, up-scale salon needs eye-catching, unique business cards.

We are looking for a unique business card design for our stylist but that can also be multi functional and used for appointment reminder and referrals. I will need a design in a format that I can modify names and titles going forward. In the past we have had a dark background with the logo on one side, and stylist and contact information on the other but we are open to all ideas. I have included our mission statement as well as branded colors below. The statement doesn't need to go on the card, it's just a reference for target market. We need space for the stylists name, title, instagram handle and then the salons phone number, website and address. I am also open to adding a spot for a qr code linked to the stylist instagram or the salon booking link.

primary brand colors:
#333333 #233415 #36502a #93874a #000000
Mission statement:
Vessolin Hair Studio, a high-end salon located in the lively Downtown Farmington, Michigan, is committed to providing exceptional services in a welcoming and relaxed environment to meet the needs of our diverse clientele.
Our salon specializes in contemporary custom haircuts, coloring, extensions, and barbering and beard grooming services. Our team of skilled stylists is passionate and inventive in their hair styling techniques. At the heart of our salon are values centered on quality, innovation, creativity, and above all, comfort. These core values are evident in every appointment across our customizable array of services.
Our goal is to establish a benchmark for exceptional hair care for every human.
Website: www.vessolinhairstudio.example
instagram: @vessolinhairstudio
address: 41782 Pelham Crest Rd, Farmington MI
phone: 248-613-4087

Industry/Entity Type

Hair Salon

Contact Information for Business Card

Stylist name, title, phone, instagram, website, address, (optional qr code)

Requirements
Should not have
• Does not need mission statement on the card.

```html
<!DOCTYPE html>
<html lang="en">
<head>
<meta charset="utf-8">
<title>Vessolin Hair Studio – Business Card</title>
<link rel="stylesheet" href="https://fonts.googleapis.com/css2?family=Montserrat:wght@400;500;700&display=swap">
<style>
  :root {
    --backdrop: #e4e3e0;
    --paper: #ffffff;
    --gold: #93874a;
    --gold-light: #b3a560;
    --gold-deep: #857a40;
    --ink: #333333;
    --ink-soft: #555555;
  }
  * { box-sizing: border-box; margin: 0; padding: 0; }
  html, body {
    width: 1200px; height: 801px; overflow: hidden;
    background: var(--backdrop);
    font-family: "Montserrat", sans-serif;
  }
  .sheet {
    position: relative; width: 1200px; height: 801px;
    display: flex; align-items: center; justify-content: center; gap: 44px;
  }
  .card {
    position: relative; width: 530px; height: 303px;
    border-radius: 4px; overflow: hidden;
    box-shadow: 0 6px 18px rgba(0,0,0,0.12);
  }
  /* Front */
  .card-front { background: var(--paper); }
  .card-front .edge-tab {
    position: absolute; left: 0; top: 262px; width: 12px; height: 26px;
    background: var(--gold); border-radius: 0 5px 5px 0;
  }
  .stylist { position: absolute; left: 40px; top: 52px; }
  .stylist-name {
    color: var(--gold); font-weight: 700; font-size: 21px; letter-spacing: 0.5px;
    text-transform: uppercase;
  }
  .stylist-title { color: var(--ink-soft); font-size: 14px; margin-top: 4px; }
  .address {
    position: absolute; left: 40px; top: 136px;
    color: var(--ink-soft); font-size: 13px; line-height: 1.5;
  }
  .contact-list {
    position: absolute; left: 40px; top: 196px; list-style: none;
    color: var(--ink-soft); font-size: 13px; line-height: 1;
  }
  .contact-list li { display: flex; align-items: center; gap: 9px; margin-bottom: 10px; }
  .contact-list svg { width: 13px; height: 13px; flex: none; }
  .brand-front {
    position: absolute; right: 40px; top: 0; bottom: 0; width: 200px;
    display: flex; align-items: center; justify-content: center;
    text-align: center;
    color: var(--gold); font-weight: 500; font-size: 22px; line-height: 1.3;
    letter-spacing: 2px; text-transform: uppercase;
  }
  /* Back */
  .card-back {
    background: var(--gold);
  }
  .card-back .surface {
    position: absolute; inset: 0;
    background: linear-gradient(120deg, var(--gold-deep) 0%, var(--gold) 45%, var(--gold-light) 100%);
  }
  .brand-back {
    position: absolute; inset: 0;
    display: flex; align-items: center; justify-content: center; gap: 14px;
    color: #ffffff; font-weight: 500; font-size: 24px; letter-spacing: 2px;
    text-transform: uppercase;
  }
  .brand-back .mark-ring {
    width: 18px; height: 18px; border: 2px solid #ffffff; border-radius: 50%;
  }
</style>
</head>
<body>
<main class="sheet">
  <section class="card card-front" aria-label="Card front">
    <span class="edge-tab"></span>
    <div class="stylist">
      <p class="stylist-name">Marisol Devane</p>
      <p class="stylist-title">President</p>
    </div>
    <p class="address">41782 Pelham Crest Rd<br>Farmington MI</p>
    <ul class="contact-list">
      <li>
        <svg viewBox="0 0 16 16" aria-hidden="true"><path fill="#93874a" d="M3.6 1.2l2.3 2.6-1.3 1.8c.9 2 2.4 3.6 4.4 4.6l1.8-1.3 2.6 2.3-1.4 2.3C6.9 13.6 2.4 9 1.3 3z"/></svg>
        248-613-4087
      </li>
      <li>
        <svg viewBox="0 0 16 16" aria-hidden="true"><circle cx="8" cy="8" r="6.5" fill="none" stroke="#93874a" stroke-width="2"/></svg>
        @vessolinhairstudio
      </li>
      <li>
        <svg viewBox="0 0 16 16" aria-hidden="true"><circle cx="8" cy="8" r="6.5" fill="none" stroke="#93874a" stroke-width="1.6"/><ellipse cx="8" cy="8" rx="2.8" ry="6.5" fill="none" stroke="#93874a" stroke-width="1.3"/><path d="M1.5 8h13" stroke="#93874a" stroke-width="1.3"/></svg>
        www.vessolinhairstudio.example
      </li>
    </ul>
    <p class="brand-front">Vessolin<br>Hair Studio</p>
  </section>

  <section class="card card-back" aria-label="Card back">
    <div class="surface" role="img" aria-label="Repeating embossed brand-mark pattern in gold foil"></div>
    <p class="brand-back"><span class="mark-ring"></span>Vessolin Hair Studio</p>
  </section>
</main>
</body>
</html>
```